Industry / Entity Type

Financial consultancy / advisers

Current site is: http://www.brightmoor-counsel.com

Looking for a complete overhaul of this site, we are after a clean modern look. Will require the ability to easily add, update and remove content, hence the WordPress design.
Example:
Add case studies
Industry documentation (downloadable brochures / flyers and such)

What we like from our current site is the colour the fonts and the logo (the city of London) we would like to have other city outlines (NYC and Tokyo, Hong Kong, Singapore).

The site will be used by our potential clients to get in contact and re-view the case studies, if possible would like to have a client login area where they can download our documents like NDA’s etc and T&C’s.

Task Outline

Create a Web Design (Coded - Design and coding required)
Designer must provide full implementation/coding depending on the platform chosen by the client (i.e. WordPress theme, HTML/CSS, bootstrap etc.)

Task Description

I need a full website built that must work on desktop and mobile. I can provide the London city skyline and the font file, which we have used. Some stock industrial photos will be required.

Requirements:

*Splash page
*What We Do
*How We do it
*Who Are We? To have the same information and links as the current site
*Why use us?
*Clients: To have the same information and links as the current site
*Partners: To have the same information and links as the current site
*Contact:

Target Market(s)

Financial institutions trading Equities, Futures, Options, Forex and Fixed Income.
Regulators, Exchanges, ECN’s
Buy side firms and Sell side firms

Industry/Entity Type

Financial

Coding

Coded - Design and coding required

Number of Pages Required

5+ page

Font styles to use
Sans Serif

Colors
f04a50

Requirements
Must have
• Splash page
• What We Do
• How We do it
• Who Are We? To have the same information and links as the current site
• Why use us?
• Clients: To have the same information and links as the current site
• Partners: To have the same information and links as the current site
• Contact:

```html
<!DOCTYPE html>
<html lang="en">
<head>
<meta charset="utf-8">
<title>Brightmoor Counsel</title>
<link rel="stylesheet" href="https://fonts.googleapis.com/css2?family=Nunito:wght@400;600;700&family=Oswald:wght@400;500&family=Open+Sans:wght@400;600&display=swap">
<style>
:root{
  --brand:#f04a50;
  --brand-deep:#c9434e;
  --ink:#222;
  --muted:#8a8a8a;
  --line:#e2e2e2;
  --panel:#f4f4f4;
  --footer:#111;
  --footer-base:#050505;
  --white:#fff;
}
*{margin:0;padding:0;box-sizing:border-box}
html,body{width:1200px;height:2605px;overflow:hidden;background:var(--white)}
body{position:relative;font-family:'Nunito',sans-serif;color:var(--ink)}
.abs{position:absolute}

/* header */
.topbar{top:0;left:0;width:1200px;height:113px}
.phone{left:90px;top:46px;font-size:21px;color:#444;display:flex;align-items:center;gap:12px}
.brand{left:465px;top:30px;width:270px;height:56px;display:flex;align-items:center;justify-content:center;gap:10px}
.brand-mark{width:14px;height:14px;background:var(--ink)}
.brand-name{font-family:'Nunito',sans-serif;font-weight:600;font-size:22px;letter-spacing:3px;text-transform:uppercase;color:var(--ink)}
.social-top{left:990px;top:47px;display:flex;gap:10px}
.social-top span{width:22px;height:22px;border-radius:3px;display:block}

.mainnav{top:113px;left:0;width:1200px;height:49px;background:var(--brand)}
.mainnav a{position:absolute;top:0;height:49px;line-height:49px;color:var(--white);font-family:'Open Sans',sans-serif;font-size:14px;text-decoration:none;transform:translateX(-50%);white-space:nowrap}
.mainnav a.active{background:#333;width:112px;text-align:center}

/* hero */
.hero{top:162px;left:0;width:1200px;height:507px;background:linear-gradient(120deg,#8b8f8a 0%,#c8c3b7 35%,#6f8a9a 60%,#3e4b5a 100%)}
.hero-title{left:89px;top:522px;font-family:'Oswald',sans-serif;font-size:44px;color:var(--white);letter-spacing:.5px}
.hero-sub{left:89px;top:574px;font-family:'Nunito',sans-serif;font-size:30px;color:var(--white)}
.hero-arrow{top:603px;width:25px;height:25px;border-radius:50%;background:#333}

/* section heads */
.sec-title{left:0;width:1200px;text-align:center;font-size:30px;color:var(--ink);font-weight:400}
.sec-sub{left:0;width:1200px;text-align:center;font-size:17px;color:var(--muted)}

/* services */
.service{top:843px;width:270px;text-align:center}
.service-icon{width:106px;height:106px;border:2px solid #bbb;border-radius:50%;margin:0 auto;display:flex;align-items:center;justify-content:center}
.service-title{margin-top:22px;font-size:16px;text-transform:uppercase;color:#333}
.service-text{margin:14px auto 0;width:250px;font-size:12.5px;line-height:20px;color:#999}

/* how we do it */
.how-photo{top:1145px;left:0;width:577px;height:368px;background:linear-gradient(135deg,#dfe6ee 0%,#a9b5c2 45%,#3b3f47 80%,#23262c 100%)}
.how-panel{top:1145px;left:577px;width:623px;height:368px;background:var(--brand-deep)}
.how-title{left:625px;top:1208px;font-size:28px;color:var(--white);text-transform:uppercase}
.how-text{left:625px;top:1253px;width:485px;font-size:13.6px;line-height:25px;color:var(--white);text-align:justify}
.btn-light{left:625px;top:1418px;width:103px;height:31px;border-radius:16px;background:var(--white);color:#444;font-size:11.5px;line-height:31px;text-align:center}

/* blog */
.card{top:1695px;width:311px;height:289px;background:var(--white);box-shadow:0 1px 5px rgba(0,0,0,.18)}
.card-photo{height:165px}
.card-date{position:absolute;left:0;top:92px;width:38px;height:73px}
.card-date .day{height:45px;background:var(--brand);color:var(--white);text-align:center;font-size:15px;line-height:22px;padding-top:4px}
.card-date .day small{display:block;font-size:8px;line-height:10px}
.card-date .year{height:28px;background:#222;color:var(--white);font-size:10px;text-align:center;line-height:28px}
.card-title{margin-top:22px;text-align:center;font-size:16px;text-transform:uppercase;color:#333}
.card-text{margin:8px auto 0;width:250px;text-align:center;font-size:10.5px;line-height:17px;color:#555}
.card-more{margin-top:9px;text-align:center;font-size:10.5px;color:var(--brand)}

/* clients */
.clients{top:2046px;left:0;width:1200px;height:275px;background:var(--panel)}
.client{top:2196px;transform:translateX(-50%);display:flex;align-items:center;gap:7px;font-size:19px;font-weight:700;color:#333;white-space:nowrap}
.client i{width:10px;height:10px;background:#333;display:block}

/* footer */
.footer{top:2321px;left:0;width:1200px;height:220px;background:var(--footer)}
.foot-brand{left:90px;top:2417px;display:flex;align-items:center;gap:9px}
.foot-brand i{width:12px;height:12px;background:var(--white);display:block}
.foot-brand span{font-size:17px;font-weight:600;letter-spacing:2.5px;color:var(--white);text-transform:uppercase}
.foot-head{top:2364px;font-size:14.5px;color:var(--white);text-transform:uppercase}
.foot-lines{left:358px;top:2402px;font-size:11px;line-height:21.5px;color:var(--white)}
.foot-note{left:659px;top:2400px;width:210px;font-size:11px;line-height:19px;color:var(--white)}
.news-input{left:659px;top:2442px;width:148px;height:31px;background:var(--white);font-size:11px;color:#999;line-height:31px;padding-left:8px}
.news-btn{left:807px;top:2442px;width:55px;height:31px;background:var(--brand);color:var(--white);font-size:11px;line-height:31px;text-align:center}
.foot-social{left:940px;top:2405px;display:flex;gap:14px}
.foot-social span{width:24px;height:24px;border-radius:3px;background:var(--white);display:block}
.base{top:2541px;left:0;width:1200px;height:64px;background:var(--footer-base);color:var(--white);font-size:13px;text-align:center;line-height:64px}
.base-tag{right:16px;top:2541px;line-height:64px;font-size:11px;color:var(--white)}
</style>
</head>
<body>

<header class="abs topbar">
  <div class="abs phone">
    <svg width="16" height="16" viewBox="0 0 16 16"><rect width="16" height="16" rx="2" fill="#f04a50"/><path d="M5 3.5l2 2-1 1.3c.6 1.3 1.6 2.4 3 3l1.2-1 2 2-1.2 1.7C7.5 12.3 3.8 8.6 3.5 5z" fill="#fff"/></svg>
    <span>(08) 9400 1187</span>
  </div>
  <div class="abs brand"><span class="brand-mark"></span><span class="brand-name">Brightmoor Counsel</span></div>
  <div class="abs social-top" aria-label="Social links">
    <span style="background:#3b6fb6"></span><span style="background:#29a9e1"></span><span style="background:#2a77b5"></span><span style="background:#d9413a"></span>
  </div>
</header>

<nav class="abs mainnav">
  <a class="active" style="left:145px">HOME</a>
  <a style="left:262px">WHAT WE DO</a>
  <a style="left:412px">HOW WE DO IT</a>
  <a style="left:559px">WHO ARE WE</a>
  <a style="left:698px">WHY USE US</a>
  <a style="left:822px">CLIENTS</a>
  <a style="left:936px">PARTNERS</a>
  <a style="left:1056px">CONTACT</a>
</nav>

<section class="abs hero" role="img" aria-label="Photo of three colleagues working together at a laptop in a bright office"></section>
<h1 class="abs hero-title">BRIGHTMOOR COUNSEL</h1>
<p class="abs hero-sub">Neque porro quisquam est qui</p>
<div class="abs hero-arrow" style="left:1029px"><svg width="25" height="25"><path d="M14.5 8l-4.5 4.5 4.5 4.5" stroke="#fff" stroke-width="2" fill="none"/></svg></div>
<div class="abs hero-arrow" style="left:1063px"><svg width="25" height="25"><path d="M10.5 8l4.5 4.5-4.5 4.5" stroke="#fff" stroke-width="2" fill="none"/></svg></div>

<h2 class="abs sec-title" style="top:736px">WHAT WE DO</h2>
<p class="abs sec-sub" style="top:776px">porro quisquam est qui dolorem</p>

<div class="abs service" style="left:61px">
  <div class="service-icon"><svg width="36" height="30" viewBox="0 0 36 30"><rect x="6" y="4" width="24" height="16" rx="1.5" fill="none" stroke="#f04a50" stroke-width="2.5"/><path d="M2 24h32" stroke="#f04a50" stroke-width="3" stroke-linecap="round"/></svg></div>
  <h3 class="service-title">Product Development</h3>
  <p class="service-text">It has survived not only five centuries, but also the leap into electronic typesetting, remaining</p>
</div>
<div class="abs service" style="left:329px">
  <div class="service-icon"><svg width="44" height="34" viewBox="0 0 44 34"><circle cx="22" cy="9" r="6" fill="#f04a50"/><path d="M11 32c0-8 5-12 11-12s11 4 11 12z" fill="#f04a50"/><circle cx="9" cy="12" r="4.5" fill="#f04a50"/><path d="M1 30c0-6 4-9 8-9 2 0 3 .5 4 1-2 2-3 5-3 8z" fill="#f04a50"/><circle cx="35" cy="12" r="4.5" fill="#f04a50"/><path d="M43 30c0-6-4-9-8-9-2 0-3 .5-4 1 2 2 3 5 3 8z" fill="#f04a50"/></svg></div>
  <h3 class="service-title">Interim Management</h3>
  <p class="service-text">It has survived not only five centuries, but also the leap into electronic typesetting, remaining</p>
</div>
<div class="abs service" style="left:600px">
  <div class="service-icon"><svg width="32" height="36" viewBox="0 0 32 36"><path d="M4 3h14l6 6v18H4z" fill="none" stroke="#f04a50" stroke-width="2.5"/><path d="M12 10h12l6 6v17H12z" fill="#f04a50"/></svg></div>
  <h3 class="service-title">Process Outsourcing</h3>
  <p class="service-text">It has survived not only five centuries, but also the leap into electronic typesetting, remaining</p>
</div>
<div class="abs service" style="left:864px">
  <div class="service-icon"><svg width="32" height="32" viewBox="0 0 32 32"><circle cx="13" cy="13" r="8.5" fill="none" stroke="#f04a50" stroke-width="3.5"/><path d="M19.5 19.5L28 28" stroke="#f04a50" stroke-width="4.5" stroke-linecap="round"/></svg></div>
  <h3 class="service-title">Research</h3>
  <p class="service-text">It has survived not only five centuries, but also the leap into electronic typesetting, remaining</p>
</div>

<div class="abs how-photo" role="img" aria-label="Photo of a consultant working on a laptop and calculator over printed financial charts"></div>
<div class="abs how-panel"></div>
<h2 class="abs how-title">How We Do It</h2>
<p class="abs how-text">Since founding Brightmoor Counsel in 2014 we have dedicated ourselves to the provision of services. What differentiates us from other advisers or consultancies is a genuine motivation to see our clients succeed. Today's technology allows our clients to take their knowledge to the market in ways that previous generations could only dream of. That's why BMC is dedicated to seeing you choose the right technology strategy,</p>
<div class="abs btn-light">Read More »</div>

<h2 class="abs sec-title" style="top:1588px">LATEST BLOG</h2>
<p class="abs sec-sub" style="top:1630px">Neque porro quisquam est qui dolorem</p>

<article class="abs card" style="left:106px">
  <div class="card-photo" role="img" aria-label="Photo of business colleagues meeting in an office" style="background:linear-gradient(135deg,#8a7a6c,#c9bfb3 50%,#5b5a5f)"></div>
  <div class="card-date"><div class="day">02<small>JUN</small></div><div class="year">2017</div></div>
  <h3 class="card-title">Neque Porro Quisquam</h3>
  <p class="card-text">It has survived not only five centuries, but also the leap into electronic typesetting, remaining</p>
  <p class="card-more">Read More »</p>
</article>
<article class="abs card" style="left:445px">
  <div class="card-photo" role="img" aria-label="Photo of hands working at a desk with a laptop and a clock" style="background:linear-gradient(135deg,#6e5640,#d8a676 50%,#3f3a36)"></div>
  <div class="card-date"><div class="day">02<small>JUN</small></div><div class="year">2017</div></div>
  <h3 class="card-title">Neque Porro Quisquam</h3>
  <p class="card-text">It has survived not only five centuries, but also the leap into electronic typesetting, remaining</p>
  <p class="card-more">Read More »</p>
</article>
<article class="abs card" style="left:783px">
  <div class="card-photo" role="img" aria-label="Photo of a presenter showing charts to a seated team" style="background:linear-gradient(135deg,#e8ecef,#b8c6cf 50%,#3c4a58)"></div>
  <div class="card-date"><div class="day">02<small>JUN</small></div><div class="year">2017</div></div>
  <h3 class="card-title">Neque Porro Quisquam</h3>
  <p class="card-text">It has survived not only five centuries, but also the leap into electronic typesetting, remaining</p>
  <p class="card-more">Read More »</p>
</article>

<section class="abs clients"></section>
<h2 class="abs sec-title" style="top:2096px">CLIENTS</h2>
<div class="abs client" style="left:193px"><i></i>Norvale</div>
<div class="abs client" style="left:363px">Kestrel Group</div>
<div class="abs client" style="left:530px">Portlane</div>
<div class="abs client" style="left:688px">Ardent Data</div>
<div class="abs client" style="left:851px"><i></i>Tradecove</div>
<div class="abs client" style="left:1023px">Harbourline</div>

<footer class="abs footer"></footer>
<div class="abs foot-brand"><i></i><span>Brightmoor Counsel</span></div>
<h4 class="abs foot-head" style="left:358px">Contact Us</h4>
<p class="abs foot-lines">Address : Suite 4 Harrow Court,Elmfield,<br>Northbridge,Beds,NB7 2LQ<br>Phone : +44(0)20 3000 4127.<br>Email : sales@brightmoor-counsel.com</p>
<h4 class="abs foot-head" style="left:659px">Sign Up For Newsletter</h4>
<p class="abs foot-note">Your about us information would fit here nicely.</p>
<div class="abs news-input">Email address</div>
<div class="abs news-btn">Submit</div>
<h4 class="abs foot-head" style="left:940px">Follow Us Out There</h4>
<div class="abs foot-social" aria-label="Social links"><span></span><span></span><span></span><span></span></div>
<div class="abs base">Copyright © 2017. All Rights Reserved</div>
<div class="abs base-tag">C6</div>

</body>
</html>
```